Business Card Design

We need a business card designed for our new company. Prefer a black card with white logo & writing.

Contact Information for Business Card

Ted Galloway, address: 7-4812 Fernhollow Road, Abbotsford, BC, V3K 8R2, Office Phone: 604-712-3390, Cell: 604-947-2164, Email: ted@resinworkshub.ca

Colors

Designer to choose only greyscale colors for use in the design.

```html
<!DOCTYPE html>
<html lang="en">
<head>
<meta charset="utf-8">
<title>Resin Works Hub — Business Card</title>
<link href="https://fonts.googleapis.com/css2?family=Poppins:wght@400;700&display=swap" rel="stylesheet">
<style>
  :root {
    --page-bg: #2a2a2a;
    --card-black: #131313;
    --band-grey: #808080;
    --ink-white: #ffffff;
    --rule-grey: #555555;
  }
  * { margin: 0; padding: 0; box-sizing: border-box; }
  html, body {
    width: 1200px; height: 1015px; overflow: hidden;
    background: var(--page-bg);
    font-family: "Poppins", sans-serif;
    color: var(--ink-white);
  }
  .sheet {
    position: relative; width: 1200px; height: 1015px;
    display: flex; flex-direction: column; align-items: center; justify-content: center;
    gap: 60px;
  }
  .card {
    position: relative; width: 700px; height: 400px;
    background: var(--card-black);
    overflow: hidden;
    box-shadow: 0 10px 30px rgba(0,0,0,.45);
  }
  .wordmark {
    position: absolute; text-align: center;
    font-weight: 700; line-height: 1; color: var(--ink-white);
    text-transform: uppercase;
  }
  .wordmark .wordmark-main { display: block; }
  .wordmark .wordmark-sub { display: block; letter-spacing: .6em; margin-left: .6em; }

  .card-front .wordmark {
    left: 0; right: 0; top: 50%; transform: translateY(-50%);
    font-size: 52px;
  }
  .card-front .wordmark .wordmark-sub { font-size: 22px; margin-top: 14px; }

  .card-back .band { position: absolute; inset: 0; }
  .card-back .wordmark {
    left: 95px; width: 280px; top: 50%; transform: translateY(-50%);
    font-size: 34px;
  }
  .card-back .wordmark .wordmark-sub { font-size: 16px; margin-top: 10px; }

  .contact {
    position: absolute; left: 400px; top: 78px; width: 280px;
    font-size: 15px; line-height: 1.45;
  }
  .contact-name { font-size: 24px; font-weight: 700; text-transform: uppercase; letter-spacing: .02em; }
  .rule { width: 48px; height: 1px; background: var(--rule-grey); margin: 18px 0 16px; }
  .contact-line { display: flex; align-items: center; gap: 8px; }
  .contact-line svg { width: 14px; height: 14px; flex: none; fill: var(--ink-white); }
</style>
</head>
<body>
<main class="sheet">
  <section class="card card-front" aria-label="Card front">
    <div class="wordmark">
      <span class="wordmark-main">Resin Works</span>
      <span class="wordmark-sub">Hub</span>
    </div>
  </section>

  <section class="card card-back" aria-label="Card back">
    <svg class="band" viewBox="0 0 700 400" aria-hidden="true">
      <rect x="140" y="0" width="180" height="400" fill="var(--band-grey)"/>
      <polygon points="60,95 140,95 230,140 320,95 320,300 230,345 140,300 60,300" fill="var(--card-black)"/>
    </svg>
    <div class="wordmark">
      <span class="wordmark-main">Resin Works</span>
      <span class="wordmark-sub">Hub</span>
    </div>

    <div class="contact">
      <p class="contact-name">Ted Galloway</p>
      <div class="rule"></div>
      <p class="contact-line">
        <svg viewBox="0 0 24 24"><path d="M6.6 10.8a15.1 15.1 0 0 0 6.6 6.6l2.2-2.2a1 1 0 0 1 1-.25 11.4 11.4 0 0 0 3.6.57 1 1 0 0 1 1 1V20a1 1 0 0 1-1 1A17 17 0 0 1 3 4a1 1 0 0 1 1-1h3.5a1 1 0 0 1 1 1c0 1.25.2 2.45.57 3.57a1 1 0 0 1-.25 1z"/></svg>
        604-712-3390
      </p>
      <p class="contact-line">
        <svg viewBox="0 0 24 24"><path d="M7 1h10a2 2 0 0 1 2 2v18a2 2 0 0 1-2 2H7a2 2 0 0 1-2-2V3a2 2 0 0 1 2-2zm0 3v14h10V4zm5 15.5a1 1 0 1 0 0 2 1 1 0 0 0 0-2z"/></svg>
        604-947-2164
      </p>
      <p class="contact-line">
        <svg viewBox="0 0 24 24"><path d="M2 5h20v14H2zm2 2v.5l8 5 8-5V7zm0 2.9V17h16V9.9l-8 5z"/></svg>
        ted@resinworkshub.ca
      </p>
      <div class="rule"></div>
      <p>7-4812 Fernhollow Road,<br>Abbotsford, BC, V3K 8R2</p>
    </div>
  </section>
</main>
</body>
</html>
```